Need App for Impact Related Events

My app is to help with internal events. When you enter the prompted event code the next screen shows you everyone currently at the event. It will give you the ability to Start a conversation with someone you met at that event, or signal it is your turn to send a message. The next screen is a message thread with that person. I am looking for a design that incorporates the colors and ‘feel good’ emotion of our logo. I have pieced together a pretty good interpretation of what I’m looking for in the attached mockup by slicing and dicing designs. I also attached our logo mascot.Screens (see attached mockups)

Note 1: I do not like the picture on the screen used in screen one because it makes it seem like a dating app. I attached an alternative photo that can be used or present different ideas.

Note 2: On the login/signup screen (screen 2) I need an additional first and last name for login, you can try to fit this on one login screen or present a two step signup screen where that is presented in the second screen.

READ MOCKUP GUIDELINES UNDER Must Haves

Target Market(s)

People attending internal social impact events

Industry/Entity Type

Charity

Font styles to use
Sans Serif

Colors
86cfc6

Requirements
Must have
• Follow the screen mockups attached to project
• PLEASE READ
• I have provided a relatively close design of what I’m looking for in the mockups. Some screens need to be followed more closely to my design mockup than other. I have listed a guide below how how closely you should follow my mockup design exactly. Overall I would like to see some ideas of incorporating a few accent colors so it doesn’t appear SO Blue. I also attached some app inspiration designs I found from around the web
• Screen Mockup Guideline Follow %
• Screen 1: 65% - mostly on target, would like to see ways to make it not SO Blue and possibly creative places to add some explainer text describing the app
• Screen 2: 50% - general design idea is here, but more open
• Screen 3: 35% - a lot more room for design influence
• Screen 4: 70% - mostly on target, a little room for design influence/color scheme ideas
• Screen 5-6: 25% - a lot of room for design change/ideas/influence
• Screen 7-8: 80% - already very close to what I need, maybe open to slight sizing and color scheme ideas
• Screen 9: 15% - the most open for influence, only the general functionality of the screen is communicated here
Nice to have
• Please Read Mockup Guideline above. In large part I am looking for something to use some nice accent colors so it is not overwhelmingly blue and bring the whole design into a seamless style.
Should not have

```html
<!DOCTYPE html>
<html lang="en">
<head>
<meta charset="utf-8">
<title>Messages</title>
<link rel="stylesheet" href="https://fonts.googleapis.com/css2?family=Nunito+Sans:wght@400;600;700;800&display=swap">
<style>
  :root {
    --teal: #14c6c9;
    --ink: #23222e;
    --muted: #5f5f6a;
    --placeholder: #8a8a94;
    --rule: #ececef;
    --field-border: #e6e6ea;
    --bg: #ffffff;
    --avatar-warm: #8a6a5c;
    --avatar-deep: #5a4a52;
    --avatar-cool: #6c6f86;
    --avatar-grey: #9b9b9b;
  }
  * { box-sizing: border-box; margin: 0; padding: 0; }
  html, body { width: 675px; height: 1200px; overflow: hidden; background: var(--bg); }
  body { position: relative; font-family: "Nunito Sans", sans-serif; color: var(--ink); }

  .screen-title { position: absolute; left: 30px; top: 36px; font-size: 50px; font-weight: 800; letter-spacing: 0.5px; line-height: 64px; }
  .profile-avatar { position: absolute; left: 579px; top: 36px; width: 64px; height: 64px; border-radius: 50%; background: linear-gradient(135deg, #c9c9c9, var(--avatar-grey) 60%, #4a4a4a); }

  .search-field { position: absolute; left: 56px; top: 141px; width: 563px; height: 75px; border: 2px solid var(--field-border); border-radius: 12px; display: flex; align-items: center; justify-content: space-between; padding: 0 32px 0 27px; }
  .search-field span { font-size: 27px; color: var(--placeholder); letter-spacing: 0.3px; }

  .section-label { position: absolute; left: 30px; font-size: 36px; font-weight: 600; line-height: 44px; }
  .rule { position: absolute; left: 0; width: 675px; height: 2px; background: var(--rule); }

  .thread { position: absolute; left: 0; width: 675px; height: 100px; }
  .thread .avatar { position: absolute; left: 39px; top: 18px; width: 64px; height: 64px; border-radius: 50%; }
  .thread .name { position: absolute; left: 133px; top: 10px; font-size: 30px; font-weight: 600; letter-spacing: 0.4px; line-height: 38px; }
  .thread .preview { position: absolute; left: 133px; top: 54px; font-size: 26px; color: var(--muted); letter-spacing: 0.3px; line-height: 34px; }
  .thread .preview.awaiting { color: var(--teal); font-weight: 700; }
  .thread .time { position: absolute; right: 28px; top: 4px; font-size: 22px; color: var(--muted); letter-spacing: 0.5px; }

  .tab-bar { position: absolute; left: 0; top: 1080px; width: 675px; height: 120px; }
  .tab-bar svg { position: absolute; }
  .tab-dot { position: absolute; left: 193px; top: 1096px; width: 18px; height: 18px; border-radius: 50%; background: var(--teal); }
  .compose-button { position: absolute; left: 286px; top: 1084px; width: 104px; height: 104px; border-radius: 50%; background: var(--teal); display: flex; align-items: center; justify-content: center; }
</style>
</head>
<body>
  <h1 class="screen-title">Messages</h1>
  <div class="profile-avatar" role="img" aria-label="Profile photo of the signed-in user"></div>

  <div class="search-field">
    <span>Search for messages</span>
    <svg width="34" height="34" viewBox="0 0 34 34" fill="none" stroke="var(--teal)" stroke-width="3.5" stroke-linecap="round">
      <circle cx="14" cy="14" r="11"/><line x1="22" y1="22" x2="31" y2="31"/>
    </svg>
  </div>

  <h2 class="section-label" style="top:262px">Unread</h2>
  <div class="rule" style="top:326px"></div>

  <div class="thread" style="top:362px">
    <div class="avatar" role="img" aria-label="Profile photo of Nora Ellison" style="background:linear-gradient(135deg,#c8a996,var(--avatar-warm))"></div>
    <div class="name">Nora Ellison</div>
    <div class="preview awaiting">Waiting for your response.</div>
  </div>

  <div class="rule" style="top:487px"></div>
  <h2 class="section-label" style="top:520px">Chats</h2>
  <div class="rule" style="top:584px"></div>

  <div class="thread" style="top:619px">
    <div class="avatar" role="img" aria-label="Profile photo of Theo Marsh" style="background:linear-gradient(135deg,#9a7a6a,var(--avatar-deep))"></div>
    <div class="name">Theo Marsh</div>
    <div class="preview">You: Nice to meet you!</div>
    <div class="time">12:49</div>
  </div>

  <div class="rule" style="top:744px"></div>

  <div class="thread" style="top:779px">
    <div class="avatar" role="img" aria-label="Profile photo of Ruby Lane" style="background:linear-gradient(135deg,#d8c8e8,var(--avatar-cool))"></div>
    <div class="name">Ruby Lane</div>
    <div class="preview">Great, we’ll discuss this idea further.</div>
    <div class="time">03:51</div>
  </div>

  <div class="rule" style="top:906px"></div>

  <nav class="tab-bar" aria-label="Main navigation"></nav>
  <svg style="position:absolute;left:44px;top:1125px" width="50" height="50" viewBox="0 0 50 50" fill="none" stroke="var(--teal)" stroke-width="4" stroke-linecap="round" stroke-linejoin="round" aria-label="Events">
    <rect x="4" y="8" width="42" height="38" rx="5"/><line x1="4" y1="19" x2="46" y2="19"/><line x1="15" y1="3" x2="15" y2="11"/><line x1="35" y1="3" x2="35" y2="11"/>
  </svg>
  <div class="tab-dot"></div>
  <svg style="position:absolute;left:180px;top:1127px" width="46" height="46" viewBox="0 0 46 46" fill="none" stroke="var(--teal)" stroke-width="4" stroke-linejoin="round" aria-label="Messages">
    <path d="M23 4a19 19 0 1 0 0 38h19V23A19 19 0 0 0 23 4z"/>
  </svg>
  <div class="compose-button" aria-label="New conversation">
    <svg width="44" height="44" viewBox="0 0 44 44" stroke="#fff" stroke-width="5" stroke-linecap="round"><line x1="22" y1="4" x2="22" y2="40"/><line x1="4" y1="22" x2="40" y2="22"/></svg>
  </div>
  <svg style="position:absolute;left:450px;top:1124px" width="46" height="52" viewBox="0 0 46 52" fill="none" stroke="var(--teal)" stroke-width="4" stroke-linecap="round" stroke-linejoin="round" aria-label="Notifications">
    <path d="M8 38V22a15 15 0 0 1 30 0v16l4 4H4z"/><path d="M18 46a5 5 0 0 0 10 0"/><line x1="23" y1="3" x2="23" y2="7"/>
  </svg>
  <svg style="position:absolute;left:582px;top:1131px" width="50" height="38" viewBox="0 0 50 38" fill="none" stroke="var(--teal)" stroke-width="4" stroke-linecap="round" aria-label="Settings">
    <line x1="3" y1="10" x2="47" y2="10"/><line x1="3" y1="28" x2="47" y2="28"/>
    <circle cx="33" cy="10" r="6" fill="var(--teal)"/><circle cx="17" cy="28" r="6" fill="var(--teal)"/>
  </svg>
</body>
</html>
```